Law Firm Advertising Design Needed

Law Office of Dalmer K Quoss provides legal services to businesses and individuals who have been or are being injured. Our main practice area is personal injury (car accidents, wrongful death, premises liability), but we are looking for an ad that highlights a lesser known area of our practice - insurance company bad faith and breach of contract.

This ad will be placed in 8 1/2" x 11" format in a local neighborhood directory. It will also be placed in a smaller format (to be determined) in the local newspaper of a region of Arizona that has recently lost a considerable number of homes and people to wildfire.

We want to convey through the ad that our firm is available to help if their insurance company is not paying a legitimate claim or not paying enough for their claim.

Because of the tragic nature of the events in Velmont, we would like to avoid images of fire or anything resembling fire. However, the ad should capture the attention of individuals who are struggling through an insurance claim with all the stacks of paperwork and frustrated with unresponsive adjusters and unreasonably low offers.

The design should convey a feeling of safety, security and being taken care of.

Information that must be included in the ad are: the firm name (Law Office of Dalmer K Quoss), address (47390 N 18th Street, Ste 506, Phoenix, AZ 85044), the phone number (602-514-7730) and the fact that we have mobile offices available to assist in your area.

An example of text that has been used in the past is here:
"If your own insurance company is refusing to pay what you are owed on a claim, call the Law Office of Dalmer K Quoss. We fight for you by examining the reasons your insurance carrier is denying or making an insufficient offer on the claim; updating and correcting claim documentation; making a new demand and filing a lawsuit if necessary. Whether it's a simple misunderstanding or something more complicated, we can help!

Here are a few of the kinds of claims we handle:
- Hit and Run or Uninsured driver claims
- Fire, flood and property loss
- Life insurance benefits
- Health insurance claims
- Catastrophic losses
- Business insurance
- Wrongful Death Benefits

Our attorneys are available to help you cut through the nonsense. Call to make an appointment for a free consultation with an attorney today. "

An example of a previous ad for car accident services is attached for reference.
Updates

Hi Everyone,

The main lawyer involved in the decision making process has been giving me some feedback in general on the designs that I thought I would pass along.  He does not want the name of the law firm to be the first thing you notice when you look at the ad. Try to keep that small and possibly to the bottom of the ad. The phone number should be rather large, but the address should be rather small (we are required by the Lawyers' Guild to include our address, but we don't want our location to limit the location of our clients because our mobile offices can travel to them).  He would prefer that the logo either not be included or be not a significant part of the ad.

                                   

Thanks!  I will continue providing individual feedback to ads received. 

Target Market(s)

Low to middle income residents of the State of Arizona with little or no college education

Industry/Entity Type

Insurance

```html
<!DOCTYPE html>
<html lang="en">
<head>
<meta charset="utf-8">
<title>Law Office of Dalmer K Quoss – Insurance Claim Help</title>
<link href="https://fonts.googleapis.com/css2?family=Cinzel:wght@600&family=Roboto:wght@400;500;700&display=swap" rel="stylesheet">
<style>
  :root {
    --frame: #7a7a7a;
    --panel: #575757;
    --panel-dark: #4a4a4a;
    --band: #d6d6d6;
    --ink: #111111;
    --white: #ffffff;
    --soft: #e6e6e6;
    --ribbon: #0d0d0d;
    --divider: #bdbdbd;
  }
  * { margin: 0; padding: 0; box-sizing: border-box; }
  html, body { width: 927px; height: 1200px; overflow: hidden; background: var(--frame); }
  .ad {
    position: relative; width: 927px; height: 1200px; overflow: hidden;
    background: var(--frame);
    font-family: "Roboto", Arial, sans-serif;
  }
  .hero-photo {
    position: absolute; left: 15px; top: 0; width: 897px; height: 487px;
    background: linear-gradient(160deg, #cfcfcf 0%, #ececec 35%, #dedede 65%, #b5b5b5 100%);
  }
  .lower-bg {
    position: absolute; left: 15px; top: 487px; width: 897px; height: 145px;
    background: linear-gradient(to bottom, #6e6e6e, #4f4f4f);
  }
  .quote-card {
    position: absolute; left: 38px; top: 405px; width: 850px; height: 185px;
    transform: rotate(-2.2deg);
    background: linear-gradient(to bottom, #e3e3e3, #a9a9a9);
    border: 3px solid var(--white); border-radius: 14px;
    box-shadow: 0 4px 10px rgba(0,0,0,.45);
    display: flex; align-items: center; justify-content: center;
    padding: 0 52px;
    text-align: center; font-size: 20px; line-height: 28px; color: var(--ink);
  }
  .quote-card em { font-style: italic; }
  .firm-band {
    position: absolute; left: 15px; top: 632px; width: 897px; height: 84px;
    background: var(--band);
    display: flex; align-items: center; justify-content: center;
    font-family: "Cinzel", "Times New Roman", serif; font-weight: 600;
    font-size: 44px; color: var(--ink); letter-spacing: 1px;
  }
  .services {
    position: absolute; left: 15px; top: 716px; width: 897px; height: 359px;
    background: linear-gradient(to bottom, var(--panel), var(--panel-dark));
  }
  .claims { position: absolute; left: 82px; top: 22px; color: var(--white); }
  .claims-intro { font-size: 17px; color: var(--soft); margin-bottom: 14px; }
  .claims-list { list-style: none; }
  .claims-list li { font-size: 18px; font-weight: 500; line-height: 28.5px; }
  .claims-list li::before { content: "\25AA"; margin-right: 6px; font-size: 14px; }
  .cta {
    position: absolute; left: 0; top: 282px; width: 560px;
    text-align: center; color: var(--white); font-size: 15px; line-height: 21px;
  }
  .cta strong { font-weight: 700; }
  .divider { position: absolute; left: 610px; top: 20px; }
  .mobile-note {
    position: absolute; left: 662px; top: 92px; width: 220px;
    text-align: center; color: var(--white);
    font-weight: 700; font-size: 25px; line-height: 38px;
  }
  .phone-ribbon { position: absolute; left: 0; top: 1075px; }
  .phone {
    position: absolute; left: 0; top: 1075px; width: 893px; height: 83px;
    display: flex; align-items: center; justify-content: center;
    color: var(--white); font-size: 60px; letter-spacing: 1px;
  }
  .address {
    position: absolute; left: 0; top: 1168px; width: 927px;
    text-align: center; color: var(--soft); font-size: 14.5px;
  }
</style>
</head>
<body>
<main class="ad">
  <div class="hero-photo" role="img" aria-label="Photo of an insurance claim form on a desk with a large DENIED stamp across it"></div>

  <div class="lower-bg"></div>
  <blockquote class="quote-card">
    <p>“If your own insurance company is refusing to pay what you are owed on a claim, call the Law Office of Dalmer K Quoss. We fight for you to get every penny you deserve. Whether it’s a simple misunderstanding or something more complicated, <em>we can help!</em>”</p>
  </blockquote>

  <h1 class="firm-band">Law Office of Dalmer K. Quoss</h1>

  <section class="services">
    <div class="claims">
      <p class="claims-intro">Here are a few of the kinds of claims we handle:</p>
      <ul class="claims-list">
        <li>Hit and Run or Uninsured driver claims</li>
        <li>Fire, flood and property loss</li>
        <li>Life insurance benefits</li>
        <li>Health insurance claims</li>
        <li>Catastrophic losses</li>
        <li>Business insurance</li>
        <li>Wrongful Death Benefits</li>
      </ul>
    </div>
    <p class="cta">Our attorneys are available to help you cut through the nonsense.<br><strong>Call to make an appointment for a FREE CONSULTATION<br>with an attorney, Today!</strong></p>
    <svg class="divider" width="14" height="330" viewBox="0 0 14 330" aria-hidden="true">
      <line x1="7" y1="6" x2="7" y2="322" stroke="#bdbdbd" stroke-width="2"/>
      <circle cx="7" cy="6" r="5.5" fill="#bdbdbd"/>
      <circle cx="7" cy="322" r="5.5" fill="#bdbdbd"/>
    </svg>
    <p class="mobile-note">We have<br>mobile offices<br>available to<br>assist in<br>your area.</p>
  </section>

  <svg class="phone-ribbon" width="927" height="83" viewBox="0 0 927 83" aria-hidden="true">
    <polygon points="0,0 893,0 822,41.5 893,83 0,83" fill="#0d0d0d"/>
  </svg>
  <p class="phone">602-514-7730</p>
  <p class="address">47390 N 18th Street, Ste 506, Phoenix, AZ 85044</p>
</main>
</body>
</html>
```